Business Card for Professional Photographer

I'm looking for an eye catching modern clean design that compliments my logo/ website fonts & colours.
I specialise in architecture, corporate & commercial photography so I'm marketing to professional clients rather than portrait / wedding clients.

I would prefer to not have a solid black design.

My logo brand guide is as follows :

Main front font. : Reislust
Main font colour : #fff
Slogan front font : Ubuntu Bold
Monogram front font : Venti Medium
Container colour : #fff

I need print ready files in pdf .png & .eps formats.

Included in the files below are some screen grabs as reference to font & colours etc.

```html
<!DOCTYPE html>
<html lang="en">
<head>
<meta charset="utf-8">
<title>Northlight Studio – Business Card</title>
<link rel="stylesheet" href="https://fonts.googleapis.com/css2?family=Roboto:wght@400&family=Saira+Condensed:wght@700&display=swap">
<style>
  :root {
    --stage: #b5b5b5;
    --card-dark: #14161a;
    --card-dark-soft: #2a2c30;
    --gold: #c9a861;
    --gold-deep: #b88f4e;
    --gold-light: #ecd58f;
    --gold-pale: #e9d27f;
    --paper: #f1f1f1;
    --ink: #111111;
    --brand-grey: #3d3d3d;
  }
  * { box-sizing: border-box; margin: 0; padding: 0; }
  html, body { width: 1200px; height: 576px; overflow: hidden; }
  body { background: var(--stage); position: relative; }

  .card {
    position: absolute;
    top: 138px;
    width: 484px;
    height: 294px;
    border-radius: 10px;
    overflow: hidden;
    box-shadow: 0 3px 6px rgba(0,0,0,0.3);
  }

  /* Brand lockup */
  .brand { position: absolute; display: flex; flex-direction: column; }
  .brand__row { display: flex; align-items: center; }
  .brand__square { flex: none; background: var(--gold); }
  .brand__name {
    font-family: "Roboto", sans-serif; font-weight: 400;
    white-space: nowrap; line-height: 1;
  }
  .brand__tagline {
    font-family: "Roboto", sans-serif; font-weight: 400;
    white-space: nowrap; color: var(--gold-deep);
  }

  /* Front */
  .card--front { left: 82px; background: var(--card-dark); }
  .front__imagery {
    position: absolute; inset: 0;
    background: linear-gradient(125deg, var(--card-dark-soft) 0%, #1c1d21 45%, #25272b 70%, #17181b 100%);
  }
  .brand--front { left: 86px; top: 118px; }
  .brand--front .brand__square { width: 16px; height: 16px; margin-right: 14px; }
  .brand--front .brand__name { font-size: 30px; color: var(--gold); }
  .brand--front .brand__tagline { font-size: 11px; letter-spacing: 0.6px; margin: 10px 0 0 30px; }
  .front__web {
    position: absolute; left: 0; right: 0; top: 256px; text-align: center;
    font-family: "Roboto", sans-serif; font-weight: 400;
    font-size: 13px; letter-spacing: 1.5px; color: var(--gold);
  }

  /* Back */
  .card--back { left: 602px; height: 292px; background: var(--paper); }
  .back__panel { position: absolute; inset: 0; }
  .back__name {
    position: absolute; left: 27px; top: 30px;
    font-family: "Saira Condensed", sans-serif; font-weight: 700;
    font-size: 21px; color: var(--ink); line-height: 1;
  }
  .back__role {
    position: absolute; left: 27px; top: 56px;
    font-family: "Roboto", sans-serif; font-size: 12.5px; color: var(--ink);
  }
  .contact {
    position: absolute; left: 27px; top: 184px;
    list-style: none;
    font-family: "Roboto", sans-serif; font-size: 12.5px; color: var(--ink);
  }
  .contact__item { display: flex; align-items: center; height: 18.5px; white-space: nowrap; }
  .contact__icon { width: 11px; height: 11px; margin-right: 13px; flex: none; }
  .contact__address { margin-top: 6px; }

  .brand--back { left: 276px; top: 128px; width: 186px; align-items: center; }
  .brand--back .brand__square { width: 12px; height: 12px; margin-right: 9px; }
  .brand--back .brand__name { font-size: 21px; color: var(--brand-grey); }
  .brand--back .brand__tagline { font-size: 9px; letter-spacing: 0.4px; margin-top: 9px; }
</style>
</head>
<body>

  <section class="card card--front">
    <div class="front__imagery" role="img" aria-label="Darkened collage of architecture and commercial photographs"></div>
    <div class="brand brand--front">
      <div class="brand__row">
        <span class="brand__square"></span>
        <span class="brand__name">Northlight Studio</span>
      </div>
      <div class="brand__tagline">Buildings · Business · Brands</div>
    </div>
    <div class="front__web">www.northlightstudio.com.au</div>
  </section>

  <section class="card card--back">
    <svg class="back__panel" width="484" height="292" viewBox="0 0 484 292">
      <defs>
        <linearGradient id="goldPanel" x1="0" y1="0" x2="1" y2="0.3">
          <stop offset="0" stop-color="var(--gold-deep)"/>
          <stop offset="0.55" stop-color="var(--gold)"/>
          <stop offset="1" stop-color="var(--gold-light)"/>
        </linearGradient>
      </defs>
      <path d="M0 0 H268 Q232 146 276 292 H0 Z" fill="var(--gold-pale)"/>
      <path d="M0 0 H262 Q226 146 270 292 H0 Z" fill="url(#goldPanel)"/>
    </svg>

    <div class="back__name">Marcus Hale</div>
    <div class="back__role">Photographer</div>

    <ul class="contact">
      <li class="contact__item">
        <svg class="contact__icon" viewBox="0 0 12 12"><path d="M1 4 Q6 0 11 4 L9.5 5.5 L8 4.5 V3.5 H4 V4.5 L2.5 5.5 Z M2.5 6 H9.5 L10.5 11 H1.5 Z" fill="var(--ink)"/><circle cx="6" cy="8.3" r="1.3" fill="var(--gold)"/></svg>
        0412 555 019
      </li>
      <li class="contact__item">
        <svg class="contact__icon" viewBox="0 0 12 12"><rect x="0.5" y="2" width="11" height="8" fill="var(--ink)"/><path d="M0.8 2.3 L6 6.6 L11.2 2.3" stroke="var(--gold)" stroke-width="1" fill="none"/></svg>
        hello@northlightstudio.com.au
      </li>
      <li class="contact__item">
        <svg class="contact__icon" viewBox="0 0 12 12"><circle cx="6" cy="6" r="5.3" fill="var(--ink)"/><g stroke="var(--gold)" stroke-width="0.7" fill="none"><ellipse cx="6" cy="6" rx="2.2" ry="5.2"/><line x1="0.8" y1="6" x2="11.2" y2="6"/><line x1="6" y1="0.8" x2="6" y2="11.2"/></g></svg>
        www.northlightstudio.com.au
      </li>
      <li class="contact__item contact__address">27 Harbour Rd Portland Vic 3305</li>
    </ul>

    <div class="brand brand--back">
      <div class="brand__row">
        <span class="brand__square"></span>
        <span class="brand__name">Northlight Studio</span>
      </div>
      <div class="brand__tagline">Buildings · Business · Brands</div>
    </div>
  </section>

</body>
</html>
```